Specialised investor in e-mobility and energy wants business card design

We need a business card design that fits our existing corporate design. <The look and feel must be 'sharp'/'clean', dynamic, communicate momentum, professionalism etc (as one would imagine from a firm in the financial sector). We like the idea of a reverse-side of the card that includes the logo, and the name and contact details on the other. We expect the deliverable to be whatever format might be required to be able to get cards printed directly by a service such as kelmo press. Our website is www.zub.capital

```html
<!DOCTYPE html>
<html lang="en">
<head>
<meta charset="utf-8">
<title>Zub Capital – Business Card</title>
<link rel="stylesheet" href="https://fonts.googleapis.com/css2?family=Montserrat:wght@700&family=Questrial&display=swap">
<style>
  :root {
    --bg: #e8e9eb;
    --leaf: #86b24a;
    --forest: #2f5220;
    --ink: #1c1c1c;
    --paper: #ffffff;
  }
  * { margin: 0; padding: 0; box-sizing: border-box; }
  html, body { width: 1200px; height: 900px; overflow: hidden; }
  body {
    background: var(--bg);
    font-family: "Questrial", sans-serif;
    display: flex;
    flex-direction: column;
    align-items: center;
    justify-content: center;
    gap: 36px;
  }
  .card {
    position: relative;
    width: 700px;
    height: 400px;
    overflow: hidden;
    box-shadow: 0 6px 18px rgba(0,0,0,0.12);
  }
  /* Front side */
  .card--front {
    background: var(--leaf);
    display: flex;
    align-items: center;
    justify-content: center;
  }
  .brand {
    display: flex;
    align-items: center;
    gap: 14px;
    color: var(--forest);
    font-family: "Questrial", sans-serif;
  }
  .brand__dot {
    width: 22px; height: 22px;
    border-radius: 50%;
    background: var(--forest);
  }
  .card--front .brand__name { font-size: 72px; letter-spacing: 1px; }
  /* Back side */
  .card--back { background: var(--paper); }
  .card__wave { position: absolute; inset: 0; width: 100%; height: 100%; }
  .card--back .brand {
    position: absolute;
    top: 44px;
    right: 42px;
    gap: 10px;
  }
  .card--back .brand__dot { width: 14px; height: 14px; }
  .card--back .brand__name { font-size: 40px; }
  .address {
    position: absolute;
    top: 128px;
    right: 42px;
    text-align: right;
    font-size: 17px;
    line-height: 1.35;
    color: var(--ink);
  }
  .holder {
    position: absolute;
    top: 170px;
    left: 52px;
  }
  .holder__name {
    font-family: "Montserrat", sans-serif;
    font-weight: 700;
    font-size: 19px;
    letter-spacing: 0.5px;
    color: var(--leaf);
    text-transform: uppercase;
  }
  .holder__role { font-size: 17px; color: var(--ink); margin-top: 2px; }
  .contacts {
    position: absolute;
    top: 262px;
    left: 62px;
    list-style: none;
    font-size: 17px;
    color: var(--ink);
  }
  .contacts li { display: flex; align-items: center; gap: 9px; line-height: 1.45; }
  .contacts svg { width: 13px; height: 13px; fill: var(--leaf); flex: none; }
</style>
</head>
<body>

  <section class="card card--front" aria-label="Card front">
    <div class="brand">
      <span class="brand__dot"></span>
      <span class="brand__name">Zub Capital</span>
    </div>
  </section>

  <section class="card card--back" aria-label="Card back">
    <svg class="card__wave" viewBox="0 0 700 400" preserveAspectRatio="none" aria-hidden="true">
      <path d="M30,400 C250,392 420,340 520,270 C590,222 640,196 700,182 L700,400 Z" fill="var(--leaf)"/>
      <path d="M230,378 C400,368 500,285 580,228 C625,198 660,184 694,176 C662,188 628,206 598,228 C510,296 410,372 230,378 Z" fill="var(--forest)"/>
    </svg>

    <div class="brand">
      <span class="brand__dot"></span>
      <span class="brand__name">Zub Capital</span>
    </div>

    <p class="address">Zub Capital S.A.<br>Geneva, Switzerland</p>

    <div class="holder">
      <p class="holder__name">Peter Hallworth</p>
      <p class="holder__role">team directly</p>
    </div>

    <ul class="contacts">
      <li>
        <svg viewBox="0 0 16 16"><path d="M3 1h3l1.5 4-2 1.3a9 9 0 0 0 4.2 4.2L11 8.5l4 1.5v3a2 2 0 0 1-2 2A13 13 0 0 1 1 3a2 2 0 0 1 2-2z"/></svg>
        +41 79555 0182
      </li>
      <li>
        <svg viewBox="0 0 16 16"><path d="M1 3h14v10H1z M1 3l7 6 7-6" /></svg>
        peter@zub.capital
      </li>
      <li>
        <svg viewBox="0 0 16 16"><circle cx="8" cy="8" r="7"/></svg>
        www.zub.capital
      </li>
    </ul>
  </section>

</body>
</html>
```